New design for Comparison website

We need new design for our website https://prisvaktposten.no/ . We compare prices and providers in different niches such as electricity, mobile plans, broadband etc.

We would like to see design like Tarivo com or our competitor kjøpklokt no

We will need design of all pages, with tables, tables are somewhat different depending on the service compared (use kjøpklokt no for reference) . Our focus is CTR through comparison Tables.

Final design must communicate following: Professionalism, thrust, authority.

Number of Pages Required

5+ page

Font styles to use
Sans Serif

Colors

Designer to choose colors to be used in the design.

Requirements
Must have
• Tables
Nice to have
• Images in content

```html
<!DOCTYPE html>
<html lang="en">
<head>
<meta charset="utf-8">
<title>Prisvaktposten – Compare providers</title>
<link rel="stylesheet" href="https://fonts.googleapis.com/css2?family=Mulish:wght@300;400;600;700&display=swap">
<style>
:root{
  --green:#10a97b;
  --green-dark:#0d8f68;
  --blue:#17a0e3;
  --blue-card:#27a2e6;
  --yellow:#e3c500;
  --ink:#2b2b2b;
  --muted:#9a9a9a;
  --line:#d8d8d8;
  --grey-band:#efefef;
  --footer:#0b2d21;
  --white:#ffffff;
}
*{margin:0;padding:0;box-sizing:border-box}
html,body{width:1200px;height:2980px;overflow:hidden;background:var(--white)}
body{font-family:"Mulish",Arial,sans-serif;color:var(--ink);position:relative}
.abs{position:absolute}
a{color:inherit;text-decoration:none}

/* header */
.site-header{position:absolute;left:0;top:0;width:1200px;height:106px;background:var(--white)}
.brand{position:absolute;left:122px;top:30px;display:flex;align-items:center;gap:12px;color:var(--green);font-weight:700;font-size:27px}
.brand-mark{width:34px;height:34px;border-radius:50%;background:var(--green)}
.main-nav{position:absolute;left:412px;top:0;display:flex;gap:30px;height:106px;align-items:center;font-size:16px;color:#555}
.main-nav a.active{color:var(--green);position:relative}
.main-nav a.active::before{content:"";position:absolute;left:0;right:0;top:-53px;height:3px;background:var(--green)}

/* hero */
.hero{position:absolute;left:0;top:106px;width:1200px;height:584px;background:linear-gradient(110deg,#8a8480 0%,#5a4d45 35%,#3a4a66 65%,#33527e 100%)}
.hero-text{position:absolute;left:0;width:1200px;text-align:center;color:var(--white)}
.hero-title{top:190px;font-size:44px;font-weight:400}
.hero-sub{top:244px;font-size:36px;font-weight:400}
.hero-btn{position:absolute;left:506px;top:314px;width:178px;height:46px;border:2px solid var(--white);color:var(--white);font-size:17px;display:flex;align-items:center;justify-content:center}
.dots{position:absolute;left:542px;top:544px;display:flex;gap:8px}
.dots span{width:14px;height:14px;border-radius:50%;background:var(--white)}
.dots span.off{background:transparent;border:2px solid var(--white)}

/* section titles */
.section-title{position:absolute;left:0;width:1200px;text-align:center;font-size:29px;font-weight:400;color:var(--ink)}

/* steps */
.step{position:absolute;top:796px;width:286px;height:244px;border:2px solid var(--line);border-radius:16px;text-align:center}
.step-icon{position:absolute;left:91px;top:22px;width:104px;height:104px;border-radius:50%;background:var(--green)}
.step-num{position:absolute;left:90px;top:20px;width:28px;height:28px;border-radius:50%;background:var(--green-dark);color:var(--white);font-size:14px;font-weight:700;display:flex;align-items:center;justify-content:center;border:2px solid var(--white)}
.step-icon svg{position:absolute;left:22px;top:22px}
.step h3{position:absolute;left:0;right:0;top:144px;font-size:19px;font-weight:400}
.step p{position:absolute;left:20px;right:20px;top:174px;font-size:12.5px;line-height:20px;color:var(--muted)}

/* categories band */
.categories{position:absolute;left:0;top:1096px;width:1200px;height:382px;background:linear-gradient(100deg,var(--green) 0%,#0fae8e 45%,var(--blue) 100%);color:var(--white)}
.notch{position:absolute;left:578px;top:1096px;width:0;height:0;border-left:22px solid transparent;border-right:22px solid transparent;border-top:26px solid var(--white)}
.cat-title{position:absolute;left:0;top:58px;width:1200px;text-align:center;font-size:25px;font-weight:400}
.cat{position:absolute;top:158px;text-align:center;font-size:18px;transform:translateX(-50%);white-space:nowrap}
.cat svg{display:block;margin:0 auto 14px}
.view-more{position:absolute;left:526px;top:314px;width:152px;height:34px;border:2px solid var(--white);font-size:14px;display:flex;align-items:center;justify-content:center;letter-spacing:.5px}

/* comparison cards */
.plan{position:absolute;top:1588px;width:268px;height:306px;border-radius:14px;text-align:center;color:var(--white);border:6px solid rgba(0,0,0,.08)}
.plan.mobile{left:180px;background:var(--blue-card)}
.plan.electric{left:466px;background:var(--green)}
.plan.broadband{left:754px;background:var(--yellow)}
.plan svg{position:absolute;left:50%;top:24px;transform:translateX(-50%)}
.plan h3{position:absolute;left:0;right:0;top:96px;font-size:20px;font-weight:400}
.plan p{position:absolute;left:40px;right:40px;top:130px;font-size:12px;line-height:20px}
.plan .learn{position:absolute;left:62px;top:232px;width:132px;height:40px;border:2px solid var(--white);border-radius:12px;font-size:14px;display:flex;align-items:center;justify-content:center}

/* testimonials */
.divider{position:absolute;left:0;top:1934px;width:1200px;height:2px;background:#ddd}
.testimonials{position:absolute;left:0;top:1936px;width:1200px;height:362px;background:var(--grey-band)}
.avatar{position:absolute;left:208px;top:122px;width:160px;height:160px;border-radius:50%;background:linear-gradient(160deg,#e2e4e6,#c7ccd1)}
.quote{position:absolute;left:382px;top:140px;width:636px;font-size:17px;line-height:30px;color:#333}
.author{position:absolute;left:382px;top:254px;font-size:16px;font-weight:700}
.arrow{position:absolute;top:170px}

/* newsletter */
.news-title{position:absolute;left:0;top:2354px;width:1200px;text-align:center;font-size:30px;color:var(--green)}
.news-sub{position:absolute;left:0;top:2406px;width:1200px;text-align:center;font-size:18px;color:#888}
.news-input{position:absolute;left:270px;top:2454px;width:496px;height:44px;border:2px solid #ccc;background:#f3f3f3;display:flex;align-items:center;padding-left:18px;gap:12px;font-size:12px;color:#888}
.news-btn{position:absolute;left:774px;top:2454px;width:154px;height:44px;background:var(--green);color:var(--white);font-size:15px;display:flex;align-items:center;justify-content:center;letter-spacing:.3px}

/* footer */
.site-footer{position:absolute;left:0;top:2580px;width:1200px;height:400px;background:var(--footer);color:#cfd8d4}
.foot-col{position:absolute;top:68px}
.foot-col h4{font-size:17px;font-weight:400;color:var(--white);margin-bottom:12px;letter-spacing:.3px}
.foot-col li{list-style:none;font-size:15px;line-height:32px}
.social{display:flex;gap:10px;margin-top:6px}
.social span{width:36px;height:36px;border-radius:50%;border:2px solid #dfe6e3}
.foot-brand{position:absolute;left:710px;top:190px;display:flex;align-items:center;gap:12px;color:var(--green);font-weight:700;font-size:24px}
.foot-brand .brand-mark{width:30px;height:30px}
.foot-line{position:absolute;left:144px;top:308px;width:960px;height:1px;background:#2f4d42}
.copyright{position:absolute;left:0;top:346px;width:1200px;text-align:center;font-size:12px;color:#8aa097}
</style>
</head>
<body>

<header class="site-header">
  <a class="brand" href="#"><span class="brand-mark"></span>Prisvaktposten</a>
  <nav class="main-nav">
    <a class="active" href="#">Home</a>
    <a href="#">Broadband</a>
    <a href="#">MMS</a>
    <a href="#">Current</a>
    <a href="#">Hosting &amp; Domain</a>
    <a href="#">Residential Alarm</a>
  </nav>
</header>

<section class="hero" role="img" aria-label="Photo of a smiling man in a checked shirt using a laptop in a café">
  <h1 class="hero-text hero-title">Morbi diam mauris viverra in</h1>
  <p class="hero-text hero-sub">gravida eu mattis in ante</p>
  <a class="hero-btn" href="#">Compare Now</a>
  <div class="dots"><span class="off"></span><span></span><span></span><span></span></div>
</section>

<h2 class="section-title" style="top:730px">How it Works</h2>

<div class="step" style="left:153px">
  <div class="step-icon">
    <svg width="60" height="60" viewBox="0 0 60 60" fill="none" stroke="#fff" stroke-width="2.5">
      <circle cx="30" cy="30" r="20" stroke-dasharray="5 5"/>
      <circle cx="30" cy="10" r="4" fill="#fff"/><circle cx="30" cy="50" r="4" fill="#fff"/>
      <circle cx="10" cy="30" r="4" fill="#fff"/><circle cx="50" cy="30" r="4" fill="#fff"/>
    </svg>
  </div>
  <span class="step-num">1</span>
  <h3>Select Category</h3>
  <p>We collect the most relevant information about the service in one place</p>
</div>

<div class="step" style="left:461px">
  <div class="step-icon">
    <svg width="60" height="60" viewBox="0 0 60 60" fill="none" stroke="#fff" stroke-width="2.5">
      <circle cx="18" cy="12" r="5"/><circle cx="42" cy="48" r="5"/>
      <path d="M18 17v14h24v12" stroke-dasharray="4 4"/>
      <path d="M36 8h10M40 4l-4 4 4 4M24 52h-8"/>
    </svg>
  </div>
  <span class="step-num">2</span>
  <h3>Compare Providers</h3>
  <p>The best and most reputable players compared so you can choose the one</p>
</div>

<div class="step" style="left:769px">
  <div class="step-icon">
    <svg width="60" height="60" viewBox="0 0 60 60" fill="none" stroke="#fff" stroke-width="2.5">
      <path d="M8 26l22-16 22 16v24H8z"/>
      <path d="M8 26l22 14 22-14"/>
      <rect x="22" y="18" width="16" height="14"/>
    </svg>
  </div>
  <span class="step-num">3</span>
  <h3>Order Service</h3>
  <p>Order the service and enjoy that you’ve got the best provider quickly and easily.</p>
</div>

<section class="categories">
  <h2 class="cat-title">Look through the Available Categories</h2>

  <div class="cat" style="left:222px">
    <svg width="44" height="72" viewBox="0 0 44 72" fill="none" stroke="#fff" stroke-width="3">
      <rect x="6" y="4" width="8" height="14"/><rect x="18" y="4" width="8" height="14"/><rect x="30" y="4" width="8" height="14"/>
      <path d="M4 22h36v22a8 8 0 0 1-8 8H12a8 8 0 0 1-8-8z"/><path d="M12 32h20M12 40h20M22 52v16"/>
    </svg>Electricity</div>

  <div class="cat" style="left:380px">
    <svg width="44" height="72" viewBox="0 0 44 72" fill="none" stroke="#fff" stroke-width="3">
      <rect x="4" y="2" width="36" height="66" rx="5"/><path d="M4 12h36M4 56h36"/><circle cx="22" cy="62" r="2" fill="#fff"/>
    </svg>Mobile Plans</div>

  <div class="cat" style="left:548px">
    <svg width="76" height="72" viewBox="0 0 76 72" fill="#fff">
      <rect x="14" y="4" width="5" height="34"/><rect x="57" y="4" width="5" height="34"/>
      <rect x="2" y="38" width="72" height="24" rx="3"/><rect x="10" y="62" width="8" height="6"/><rect x="58" y="62" width="8" height="6"/>
      <rect x="12" y="46" width="6" height="6" fill="#13a8b0"/><rect x="26" y="46" width="6" height="6" fill="#13a8b0"/><rect x="40" y="46" width="6" height="6" fill="#13a8b0"/>
    </svg>Broadband</div>

  <div class="cat" style="left:740px">
    <svg width="76" height="72" viewBox="0 0 76 72" fill="none" stroke="#fff" stroke-width="3">
      <circle cx="38" cy="38" r="22"/><path d="M10 24a32 32 0 0 1 12-16M66 24a32 32 0 0 0-12-16"/>
      <path d="M38 26c6 6 8 10 8 14a8 8 0 0 1-16 0c0-4 4-8 8-14z" fill="#fff"/>
    </svg>Residential Alarm</div>

  <div class="cat" style="left:962px">
    <svg width="72" height="72" viewBox="0 0 72 72" fill="none" stroke="#fff" stroke-width="3">
      <rect x="4" y="6" width="64" height="56" rx="3"/><path d="M4 16h64"/>
      <ellipse cx="36" cy="30" rx="12" ry="4"/><path d="M24 30v22c0 2 5 4 12 4s12-2 12-4V30M24 41c0 2 5 4 12 4s12-2 12-4"/>
    </svg>Hosting &amp; Domain</div>

  <a class="view-more" href="#">VIEW MORE</a>
</section>
<div class="notch"></div>

<h2 class="section-title" style="top:1526px">Comparison Tables</h2>

<div class="plan mobile">
  <svg width="40" height="62" viewBox="0 0 40 62" fill="none" stroke="#fff" stroke-width="3"><rect x="3" y="2" width="34" height="58" rx="5"/><path d="M3 11h34M3 50h34"/></svg>
  <h3>Mobiles Plan</h3>
  <p>Class aptent taciti sociosqu ad litora torquent per conubia nostra per inceptos hymenaeos Proin nulla arcu nonummy luctus</p>
  <a class="learn" href="#">Learn More</a>
</div>
<div class="plan electric">
  <svg width="40" height="62" viewBox="0 0 44 72" fill="none" stroke="#fff" stroke-width="3"><rect x="6" y="4" width="8" height="14"/><rect x="18" y="4" width="8" height="14"/><rect x="30" y="4" width="8" height="14"/><path d="M4 22h36v22a8 8 0 0 1-8 8H12a8 8 0 0 1-8-8z"/><path d="M12 32h20M12 40h20M22 52v16"/></svg>
  <h3>Electricity Plan</h3>
  <p>Class aptent taciti sociosqu ad litora torquent per conubia nostra per inceptos hymenaeos Proin nulla arcu nonummy luctus</p>
  <a class="learn" href="#">Learn More</a>
</div>
<div class="plan broadband">
  <svg width="62" height="56" viewBox="0 0 76 72" fill="#fff"><rect x="14" y="4" width="5" height="34"/><rect x="57" y="4" width="5" height="34"/><rect x="2" y="38" width="72" height="24" rx="3"/><rect x="10" y="62" width="8" height="6"/><rect x="58" y="62" width="8" height="6"/></svg>
  <h3>Broadband Plan</h3>
  <p>Class aptent taciti sociosqu ad litora torquent per conubia nostra per inceptos hymenaeos Proin nulla arcu nonummy luctus</p>
  <a class="learn" href="#">Learn More</a>
</div>

<div class="divider"></div>
<section class="testimonials">
  <h2 class="section-title" style="top:70px">Testimonials</h2>
  <svg class="arrow" style="left:124px" width="24" height="40" viewBox="0 0 24 40" fill="none" stroke="#aaa" stroke-width="3"><path d="M20 4L6 20l14 16"/></svg>
  <div class="avatar" role="img" aria-label="Portrait photo of the reviewer"></div>
  <p class="quote">“Maecenas aliquet velit vel turpis Mauris neque metus malesuada nec ultricies sit amet porttitor mattis enim In massa libero interdum nec interdum vel blandit sed nulla”</p>
  <p class="author">By Author Name</p>
  <svg class="arrow" style="left:1046px" width="24" height="40" viewBox="0 0 24 40" fill="none" stroke="#aaa" stroke-width="3"><path d="M4 4l14 16L4 36"/></svg>
</section>

<h2 class="news-title">Sign Up for Our Newsletters</h2>
<p class="news-sub">Get news and deals delivered right to your inbox.</p>
<div class="news-input">
  <svg width="18" height="14" viewBox="0 0 18 14" fill="none" stroke="#999" stroke-width="1.5"><rect x="1" y="1" width="16" height="12"/><path d="M1 1l8 7 8-7"/></svg>
  Email address
</div>
<a class="news-btn" href="#">CLICK HERE</a>

<footer class="site-footer">
  <div class="foot-col" style="left:157px">
    <h4>COMPANY</h4>
    <ul><li>Home</li><li>About us</li><li>Contact</li><li>Terms</li><li>Privacy</li></ul>
  </div>
  <div class="foot-col" style="left:328px">
    <h4>SUBLINKS</h4>
    <ul><li>Cheap mms</li><li>Current</li><li>To me</li><li>Web hosting</li></ul>
  </div>
  <div class="foot-col" style="left:502px">
    <h4>RESOURCES</h4>
    <ul><li>Residential Alarm</li><li>Broadband</li><li>Support</li><li>Contact Us</li></ul>
  </div>
  <div class="foot-col" style="left:730px">
    <h4>STAY IN TOUCH</h4>
    <div class="social"><span></span><span></span><span></span><span></span></div>
  </div>
  <div class="foot-brand"><span class="brand-mark"></span>Prisvaktposten</div>
  <div class="foot-line"></div>
  <p class="copyright">© 2017 Company Name. All right reserved</p>
</footer>

</body>
</html>
```